Computer consultant business card

Bexil Software is a newly started computer consulting company. It's a small one-man company that provides mostly Vornix applications but also websites in collaboration with designers. I'm running this company on the side of full time university studies.

I want the final design to be clean and memorable. Be creative! :)

Some inspiration:
http://www.pixelmarta.com/design/48317
http://www.pixelmarta.com/design/2739164/business-card-design-by-frostlynk
http://www.pixelmarta.com/design/604281/business-card-design-by-koralind-vestrabanu

See attachment for my company logo.
Updates

I would like to thank everyone for submitting! I'll need a couple of days to review and ultimately select a design.

Target Market(s)

Non-technical entrepreneurs and small companies.

Industry/Entity Type

University

Requirements
Must have
• My company logo.
In any way, both colors from my logo.
First- and last name, e-mail and phone number.
Double-sided design.
Nice to have
• Something creative with the symbol in my logo

```html
<!DOCTYPE html>
<html lang="en">
<head>
<meta charset="utf-8">
<title>Bexil Software — Business Card</title>
<link rel="stylesheet" href="https://fonts.googleapis.com/css2?family=Arimo:wght@400;700&display=swap">
<style>
  :root {
    --brand-blue: #2479f4;
    --brand-dark: #323232;
    --card-white: #ffffff;
    --stage: #e9ebee;
    --text-light: #ffffff;
  }
  * { box-sizing: border-box; margin: 0; padding: 0; }
  html, body {
    width: 1200px;
    height: 823px;
    overflow: hidden;
  }
  body {
    background: var(--stage);
    font-family: "Arimo", Arial, sans-serif;
    display: flex;
    align-items: center;
    justify-content: center;
    gap: 40px;
  }
  .card {
    position: relative;
    width: 540px;
    height: 310px;
    border-radius: 22px;
    overflow: hidden;
    box-shadow: 0 6px 18px rgba(0, 0, 0, 0.18);
  }
  .card-front { background: var(--card-white); }
  .card-back { background: var(--brand-blue); }

  .front-waves {
    position: absolute;
    inset: 0;
    width: 100%;
    height: 100%;
  }
  .brand {
    position: absolute;
    left: 100px;
    top: 38px;
    display: flex;
    align-items: center;
    gap: 18px;
  }
  .brand-dot {
    width: 62px;
    height: 62px;
    border-radius: 50%;
    background: var(--brand-blue);
  }
  .brand-name {
    font-weight: 700;
    font-size: 72px;
    line-height: 1;
    color: var(--brand-dark);
    letter-spacing: -1px;
  }

  .contact {
    position: absolute;
    left: 150px;
    right: 20px;
    top: 212px;
    color: var(--text-light);
  }
  .contact-name {
    font-size: 21px;
    text-align: center;
    margin-bottom: 12px;
    padding-right: 60px;
  }
  .contact-name strong { font-weight: 700; }
  .contact-details {
    display: flex;
    justify-content: center;
    align-items: stretch;
    gap: 12px;
    font-size: 15px;
    line-height: 1.3;
    padding-right: 40px;
  }
  .contact-address { text-align: right; }
  .contact-divider {
    width: 2px;
    background: var(--text-light);
  }
  .contact-line {
    display: flex;
    align-items: center;
    gap: 6px;
  }
  .contact-line svg { width: 12px; height: 12px; fill: var(--text-light); }

  .back-brand {
    position: absolute;
    inset: 0;
    display: flex;
    align-items: center;
    justify-content: center;
    gap: 22px;
  }
  .back-brand .brand-dot {
    width: 96px;
    height: 96px;
    background: var(--card-white);
  }
  .back-brand .brand-name {
    color: var(--card-white);
    font-size: 96px;
  }
</style>
</head>
<body>
  <section class="card card-front" aria-label="Business card front">
    <svg class="front-waves" viewBox="0 0 540 310" preserveAspectRatio="none" aria-hidden="true">
      <path d="M0 158 Q260 214 540 88 L540 96 Q270 234 0 176 Z" fill="var(--brand-dark)"/>
      <path d="M0 182 Q270 238 540 102 L540 310 L0 310 Z" fill="var(--brand-blue)"/>
    </svg>

    <div class="brand">
      <span class="brand-dot"></span>
      <span class="brand-name">Bexil</span>
    </div>

    <div class="contact">
      <p class="contact-name"><strong>First Name,</strong> Last Name</p>
      <div class="contact-details">
        <div class="contact-address">
          <p>00, Complex name</p>
          <p>City, State 0042</p>
        </div>
        <span class="contact-divider"></span>
        <div class="contact-methods">
          <p class="contact-line">
            <svg viewBox="0 0 24 24" aria-hidden="true"><path d="M6.6 10.8a15 15 0 0 0 6.6 6.6l2.2-2.2a1 1 0 0 1 1-.25 11.4 11.4 0 0 0 3.6.57 1 1 0 0 1 1 1V20a1 1 0 0 1-1 1A17 17 0 0 1 3 4a1 1 0 0 1 1-1h3.5a1 1 0 0 1 1 1c0 1.25.2 2.45.57 3.57a1 1 0 0 1-.25 1z"/></svg>
            0987 654321
          </p>
          <p class="contact-line">
            <svg viewBox="0 0 24 24" aria-hidden="true"><path d="M2 6h20v12H2z M2 6l10 7 10-7" fill="none" stroke="#fff" stroke-width="2.5"/></svg>
            info@bexil.com
          </p>
        </div>
      </div>
    </div>
  </section>

  <section class="card card-back" aria-label="Business card back">
    <div class="back-brand">
      <span class="brand-dot"></span>
      <span class="brand-name">Bexil</span>
    </div>
  </section>
</body>
</html>
```